New design for Giftwell Hub Website - landing page plus 3 carousel pages

We have a new website we want to launch for 501c3 organizations - Faith-based organizations, not for profit organizations, colleges and universities. Note - this is a design only project. We want to see designs for the landing page and the 3 other pages - Faith-based organizations, not for profit organizations, colleges and universities.
Format: We expect to create this website in Wix so requirement is to make the graphics Wix compatible
See Dossier attached for more details, 4 wireframes (1 landing page and 3 carousel pages), and brand guidelines
Please be creative and and make the visuals engaging. We do NOT want you to simply replicate what is in the wireframe. We are looking for a totally new, fresh and engaging design.
Number of Pages Required
1 page
Look and feel
Each slider illustrates characteristics of the customer's brand and the style your logo design should communicate.

```html
<!DOCTYPE html>
<html lang="en">
<head>
<meta charset="utf-8">
<title>Giftwell Hub — 501c3 Organizations</title>
<link href="https://fonts.googleapis.com/css2?family=Montserrat:wght@400;500;600;700;800&family=Mulish:wght@400;600;700&display=swap" rel="stylesheet">
<style>
:root{
  --navy:#0b1a30;
  --navy-2:#10233f;
  --green:#21c17a;
  --green-dark:#2a9d55;
  --teal:#3aa39a;
  --blue:#4893d8;
  --blue-2:#3f86cf;
  --ink:#1b1b1b;
  --muted:#555;
  --white:#fff;
  --accent-line:#2f3f9a;
}
*{box-sizing:border-box;margin:0;padding:0}
html,body{width:1200px;height:4338px;overflow:hidden}
body{font-family:'Mulish',sans-serif;color:var(--ink);background:#fff;position:relative}
section,header,footer{position:absolute;left:0;width:1200px;overflow:hidden}
.abs{position:absolute}
.center{text-align:center}
h1,h2,h3,h4{font-family:'Montserrat',sans-serif}

/* HERO */
.hero{top:0;height:673px;background:radial-gradient(ellipse at 50% 0%,#2f6673 0%,#183a48 45%,#0d1f2b 100%)}
.hero-wave{left:0;top:300px;width:1200px;height:260px;background:linear-gradient(180deg,rgba(0,0,0,0) 0%,rgba(34,190,205,.45) 40%,rgba(20,140,170,.5) 60%,rgba(0,0,0,0) 100%);transform:skewY(-4deg)}
.brand{display:flex;align-items:center;gap:10px;font-family:'Montserrat',sans-serif;font-weight:600;color:#fff;font-size:26px}
.brand-dot{width:40px;height:40px;border-radius:50%;border:4px solid var(--green)}
.nav{top:33px;left:380px;display:flex;align-items:center;gap:0;font-family:'Montserrat',sans-serif;font-weight:700;font-size:12.5px;color:#fff}
.nav a{color:#fff;text-decoration:none;padding:7px 14px}
.nav .active{border:2px solid #fff;border-radius:16px;padding:6px 12px;margin-right:6px}
.nav .login{background:var(--green);border-radius:18px;padding:9px 20px;margin-left:14px}
.hero h1{top:120px;width:1200px;font-size:49px;font-weight:700;color:#fff}
.hero .lead{top:196px;width:1200px;font-family:'Montserrat',sans-serif;font-size:19px;line-height:29px;color:#fff}
.seg{width:128px;height:128px;border-radius:50%;background:radial-gradient(circle at 50% 40%,#2a5ca8,#17336a);box-shadow:0 0 30px rgba(40,120,220,.5);display:flex;align-items:center;justify-content:center}
.seg-label{width:220px;font-family:'Montserrat',sans-serif;font-weight:600;font-size:17px;line-height:25px;color:#fff}
.dots{top:620px;left:575px;display:flex;gap:9px}
.dots span{width:10px;height:10px;border-radius:50%;background:#fff}
.dots span:first-child{background:var(--green)}

/* SECTION TITLES */
.sec-title{width:1200px;font-family:'Montserrat',sans-serif;font-weight:700;font-size:23px;color:#111;letter-spacing:.5px}
.rule{width:22px;height:3px;background:var(--accent-line);left:589px}

/* PROCESS */
.process{top:673px;height:732px;background:#fff}
.step{width:220px;font-size:12.5px;line-height:18px;color:#333;text-align:center}
.step h4{font-size:13px;font-weight:700;color:#111;margin-bottom:6px}
.vline{width:1px;background:#ddd}

/* WHY ENROLL */
.enroll{top:1405px;height:509px}
.pyramid{left:0;top:0;width:634px;height:509px;background:linear-gradient(160deg,#f4f6f9 0%,#e7ebf1 100%)}
.enroll-right{left:634px;top:0;width:566px;height:509px;background:linear-gradient(200deg,#4a93d6 0%,#3ca29a 100%);color:#fff}
.enroll-right h3{position:absolute;left:47px;top:48px;font-size:23px;font-weight:700}
.enroll-right p.intro{position:absolute;left:47px;top:85px;font-size:14.5px;line-height:21px}
.feat{left:47px;display:flex;gap:14px;align-items:flex-start}
.feat h4{font-size:15px;font-weight:700}
.feat p{font-size:13.5px;margin-top:5px}

/* DONATION */
.donation{top:1914px;height:543px;background:radial-gradient(ellipse at 50% 100%,#1a3454 0%,var(--navy) 60%)}
.donation h2{top:44px;width:1200px;color:#fff;font-size:23px;font-weight:700}
.donation .sub{top:78px;width:1200px;color:#fff;font-size:15px}
.give{left:519px;top:158px;width:160px;height:40px;border:1px solid var(--teal);color:var(--green);font-family:'Montserrat',sans-serif;font-weight:700;font-size:16px;display:flex;align-items:center;justify-content:center}
.amt{top:252px;height:44px;border:1px solid var(--teal);color:var(--green);font-family:'Montserrat',sans-serif;font-size:22px;display:flex;align-items:center;justify-content:center}
.btn{background:var(--green);color:#0b1a30;font-family:'Montserrat',sans-serif;font-weight:700;border-radius:24px;display:flex;align-items:center;justify-content:center}
.pay{top:431px;height:44px;display:flex;align-items:center;justify-content:center;font-family:'Mulish',sans-serif;font-weight:700;font-size:16px;border-radius:4px}

/* DONATE WAYS */
.ways{top:2457px;height:455px;background:linear-gradient(90deg,#3f9f8f 0%,#4590d6 100%);color:#fff}
.way{width:360px;text-align:center}
.way h3{font-size:18px;font-weight:700;margin-top:14px}
.way .powered{font-size:13px;margin-top:10px;display:flex;justify-content:center;align-items:center;gap:8px}
.way p.body{font-size:14px;line-height:21px;margin-top:22px}
.way .btn{width:140px;height:42px;margin:28px auto 0;font-size:16px;color:#fff}

/* VIDEO */
.video{top:2912px;height:619px;background:#fff}
.video-frame{left:131px;top:136px;width:938px;height:428px;background:linear-gradient(120deg,#1e4c8f 0%,#2f7fc3 45%,#9cc3e4 100%)}
.play{left:570px;top:214px;width:56px;height:56px;border-radius:50%;background:#fff;display:flex;align-items:center;justify-content:center}

/* NEWSLETTER */
.news{top:3531px;height:483px}
.news-left{left:0;top:0;width:621px;height:483px;background:var(--navy);color:#fff}
.news-right{left:621px;top:0;width:579px;height:483px;background:linear-gradient(160deg,#3f7fc8,#4a97db);color:#fff;text-align:center}
.news-left h3{position:absolute;top:176px;width:621px;text-align:center;font-size:24px;line-height:35px;font-weight:700}
.email{left:134px;top:260px;width:422px;height:54px;border:2px solid #5aa0e6;border-radius:28px;display:flex;align-items:center;padding-left:24px;gap:10px;font-size:14px}
.subscribe{left:134px;top:337px;width:422px;height:54px;font-size:22px;border-radius:28px}
.consent{left:134px;top:417px;display:flex;gap:8px;align-items:center;font-size:12px}
.box{width:13px;height:13px;border:2px solid #5aa0e6}
.news-right hr{position:absolute;left:71px;width:422px;border:0;border-top:1px solid rgba(255,255,255,.7)}
.news-right h3{position:absolute;top:146px;width:579px;font-size:25px;font-weight:700}
.news-right .tag{position:absolute;top:190px;width:579px;font-size:19px;line-height:25px}
.news-right .fine{position:absolute;left:70px;top:273px;width:440px;font-size:13px;line-height:20px}

/* FOOTER */
.footer{top:4014px;height:324px;background:var(--navy);color:#fff}
.footer .about{left:131px;top:122px;width:290px;font-size:12px;line-height:19px}
.fcol{top:48px;font-size:12.5px;line-height:21px}
.fcol h5{font-family:'Montserrat',sans-serif;font-size:12.5px;font-weight:700;color:var(--green);margin-bottom:8px}
.social{display:flex;gap:24px}
.social span{width:30px;height:30px;border-radius:50%;background:#4a6fd0;display:block}
.copy{top:293px;width:1200px;text-align:center;font-size:11px}
.fline{left:131px;top:265px;width:938px;height:1px;background:rgba(255,255,255,.25)}
</style>
</head>
<body>

<header class="hero">
  <div class="abs hero-wave" role="img" aria-label="Glowing teal particle wave"></div>
  <div class="abs brand" style="left:128px;top:26px"><span class="brand-dot"></span>Giftwell Hub</div>
  <nav class="abs nav">
    <a class="active">HOME</a><a>ABOUT US</a><a>NEWSROOM</a><a>PATEMTS</a><a>CLIENTS</a><a>FAQ</a><a>CONTACT</a><a class="login">LOGIN</a>
  </nav>
  <h1 class="abs center">501c3 Organizations</h1>
  <p class="abs center lead">Lorem Ipsum is simply dummy text of the printing and<br>typesetting industry. Lorem Ipsum has been the industry's</p>

  <div class="abs seg" style="left:303px;top:346px">
    <svg width="64" height="64" viewBox="0 0 64 64" fill="none" stroke="#fff" stroke-width="2.5"><path d="M32 46 L20 34 a7 7 0 0 1 12-9 a7 7 0 0 1 12 9z"/><path d="M12 20v24l10 10M52 20v24l-10 10"/></svg>
  </div>
  <div class="abs seg-label center" style="left:257px;top:496px">Non Profit<br>Organiczation</div>

  <div class="abs seg" style="left:537px;top:374px">
    <svg width="70" height="70" viewBox="0 0 70 70" fill="none" stroke="#fff" stroke-width="2.5"><circle cx="35" cy="24" r="14"/><circle cx="24" cy="42" r="14"/><circle cx="46" cy="42" r="14"/></svg>
  </div>
  <div class="abs seg-label center" style="left:489px;top:532px">Faith Base</div>

  <div class="abs seg" style="left:777px;top:358px">
    <svg width="70" height="70" viewBox="0 0 70 70" fill="none" stroke="#fff" stroke-width="3"><path d="M5 28 L35 15 L65 28 L35 41z"/><path d="M18 34v14c10 8 24 8 34 0V34"/><path d="M62 30v14"/></svg>
  </div>
  <div class="abs seg-label center" style="left:730px;top:514px">Colleges and<br>Universities</div>

  <div class="abs dots"><span></span><span></span><span></span></div>
</header>

<section class="process">
  <div class="abs rule" style="top:34px"></div>
  <h2 class="abs center sec-title" style="top:50px">PROCESS</h2>
  <div class="abs rule" style="top:92px"></div>

  <div class="abs vline" style="left:425px;top:130px;height:240px"></div>
  <div class="abs vline" style="left:771px;top:130px;height:240px"></div>
  <div class="abs vline" style="left:599px;top:435px;height:240px"></div>

  <div class="abs step" style="left:134px;top:137px"><h4>1. LOREM IPSUM</h4>There are many variations of pass ages of Lorem Ipsum availa ble, but the majority have suffered</div>
  <div class="abs step" style="left:489px;top:137px"><h4>3. LOREM IPSUM</h4>There are many variations of pass ages of Lorem Ipsum availa ble, but the majority have suffered</div>
  <div class="abs step" style="left:831px;top:137px"><h4>5.LOREM IPSUM</h4>There are many variations of pass ages of Lorem Ipsum availa ble, but the majority have suffered</div>
  <div class="abs step" style="left:305px;top:602px"><h4>2. LOREM IPSUM</h4>There are many variations of pass ages of Lorem Ipsum availa ble, but the majority have suffered</div>
  <div class="abs step" style="left:657px;top:602px"><h4>4. LOREM IPSUM</h4>There are many variations of pass ages of Lorem Ipsum availa ble, but the majority have suffered</div>

  <svg class="abs" style="left:0;top:0" width="1200" height="732" viewBox="0 0 1200 732">
    <defs>
      <linearGradient id="pathGrad" x1="0" x2="1" y1="0" y2="0">
        <stop offset="0" stop-color="#2aa56e"/><stop offset=".6" stop-color="#3aa845"/><stop offset="1" stop-color="#3f8fd0"/>
      </linearGradient>
    </defs>
    <path d="M252 320 C300 420 380 480 424 492 C480 470 540 400 597 320 C650 400 720 470 769 492 C820 470 880 400 942 320" fill="none" stroke="url(#pathGrad)" stroke-width="36" stroke-linecap="round"/>
    <g fill="#fff" stroke="url(#pathGrad)" stroke-width="12">
      <circle cx="252" cy="320" r="80"/><circle cx="597" cy="320" r="80"/><circle cx="942" cy="320" r="80"/>
      <circle cx="424" cy="492" r="80"/><circle cx="769" cy="492" r="80"/>
    </g>
    <g fill="none" stroke="#2a7bbf" stroke-width="2.5">
      <path d="M222 318 a18 18 0 0 1 10-30 a24 24 0 0 1 44 4 a14 14 0 0 1 2 26z"/><path d="M240 318v20h-10M252 318v30M264 318v20h10"/><circle cx="228" cy="338" r="3"/><circle cx="252" cy="350" r="3"/><circle cx="276" cy="338" r="3"/>
      <circle cx="597" cy="320" r="24"/><path d="M573 320h48M597 296v48M580 306c10 6 24 6 34 0M580 334c10-6 24-6 34 0"/><rect x="563" y="286" width="68" height="68" stroke-dasharray="3 4"/>
      <circle cx="942" cy="320" r="32"/><circle cx="942" cy="320" r="18"/><circle cx="942" cy="320" r="8"/>
      <rect x="398" y="468" width="40" height="50"/><rect x="392" y="474" width="40" height="50" fill="#fff"/><path d="M400 486h24M400 494h24M400 502h14"/><circle cx="438" cy="508" r="10" fill="#fff"/><path d="M445 515l8 8"/>
      <path d="M737 490h64v34h-64zM745 474h48l8 16M737 490l8-16"/><path d="M760 500h18v8h-18z"/>
    </g>
  </svg>
</section>

<section class="enroll">
  <div class="abs pyramid" role="img" aria-label="Layered pyramid illustration: data object donor, data exchange buyer, 501c3 organizations"></div>
  <div class="enroll-right abs">
    <h3>WHY ENROLL!</h3>
    <p class="intro">To get full access to all the features,<br>start by creating an account</p>
    <div class="abs" style="left:47px;top:142px;width:22px;height:2px;background:#fff"></div>
    <div class="abs feat" style="top:200px">
      <svg width="48" height="46" viewBox="0 0 48 46" fill="none" stroke="#fff" stroke-width="2"><path d="M4 6l9-4 9 4-9 4zM4 6v10l9 4 9-4V6M26 6l9-4 9 4-9 4zM26 6v10l9 4 9-4V6M4 28l9-4 9 4-9 4zM4 28v10l9 4 9-4V28M26 28l9-4 9 4-9 4zM26 28v10l9 4 9-4V28"/></svg>
      <div><h4>Drops</h4><p>Purchase NFTs that are directly sold by top creators</p></div>
    </div>
    <div class="abs feat" style="top:296px">
      <svg width="48" height="44" viewBox="0 0 48 44" fill="none" stroke="#fff" stroke-width="2"><path d="M4 4h40l3 12H1z"/><path d="M6 16v26h36V16M18 42V28h12v14"/></svg>
      <div><h4>Marketplace</h4><p>Bid on an auction off rate digital collectibles</p></div>
    </div>
    <div class="abs feat" style="top:396px">
      <svg width="48" height="44" viewBox="0 0 48 44" fill="none" stroke="#fff" stroke-width="2"><rect x="2" y="12" width="36" height="30"/><path d="M8 12V6h36v30h-6"/></svg>
      <div><h4>My NFTs</h4><p>A digital gallery to showcase your collection</p></div>
    </div>
  </div>
</section>

<section class="donation">
  <h2 class="abs center">MY DONATION</h2>
  <p class="abs center sub">All donations are tax deductible</p>
  <div class="abs" style="left:589px;top:119px;width:22px;height:3px;background:#fff"></div>
  <svg class="abs" style="left:0;top:0" width="1200" height="300">
    <path d="M519 178H274v46M381 178v46M679 178H870v46M719 178v46M497 198v26M608 198v26" fill="none" stroke="#3aa39a" stroke-width="1.2"/>
  </svg>
  <div class="abs give">I want to give</div>
  <div class="abs amt" style="left:224px;width:92px">$25</div>
  <div class="abs amt" style="left:337px;width:92px">$50</div>
  <div class="abs amt" style="left:451px;width:94px">$100</div>
  <div class="abs amt" style="left:561px;width:94px">$125</div>
  <div class="abs amt" style="left:669px;width:94px">$150</div>
  <div class="abs amt" style="left:777px;width:199px">Other account</div>
  <div class="abs btn" style="left:443px;top:344px;width:313px;height:44px;font-size:15.5px">DONATE WITH CREDIT CARD</div>
  <div class="abs pay" style="left:222px;width:86px;color:#3b55c8">Cardline</div>
  <div class="abs pay" style="left:378px;width:80px;color:#f08a24">Orbipay</div>
  <div class="abs pay" style="left:524px;width:78px;background:#fff;color:#222;font-size:13px">Findercard</div>
  <div class="abs pay" style="left:694px;width:64px;color:#3b7ac8;font-size:11px;line-height:13px;text-align:center">Meridian Pay</div>
  <div class="abs pay" style="left:832px;width:110px;color:#1e4fa8;font-size:22px">Walletly</div>
</section>

<section class="ways">
  <div class="abs way" style="left:160px;top:40px">
    <svg width="96" height="80" viewBox="0 0 96 80" fill="none" stroke="#fff" stroke-width="2.5"><circle cx="48" cy="40" r="22"/><path d="M42 30h10a5 5 0 0 1 0 10H42zM42 40h12a5 5 0 0 1 0 10H42zM42 26v28M48 26v4M48 50v4"/><path d="M48 4v10M48 66v10M12 40h10M74 40h10M22 14l8 8M74 14l-8 8M22 66l8-8M74 66l-8-8"/></svg>
    <h3>DONATE WITH CRYPTO</h3>
    <div class="powered">Powered by GWH <span style="width:16px;height:16px;border-radius:50%;border:2px solid var(--green);display:inline-block"></span> Giftwell Hub</div>
    <p class="body">It is a long established fact that a reader will be distracted by the readable content of a page when looking at its layout. The point of using Lorem Ipsum is that it has</p>
    <div class="btn">DONATE</div>
  </div>
  <div class="abs way" style="left:668px;top:40px">
    <svg width="96" height="80" viewBox="0 0 96 80" fill="none" stroke="#fff" stroke-width="2.5"><path d="M28 44a12 12 0 0 1 4-24a18 18 0 0 1 34 2a11 11 0 0 1 2 22z"/><path d="M40 44v12h-8M48 36v30M56 44v12h8"/><circle cx="30" cy="56" r="3"/><circle cx="48" cy="70" r="3"/><circle cx="66" cy="56" r="3"/></svg>
    <h3>DONATE WITH DATA</h3>
    <p class="body" style="margin-top:26px">It is a long established fact that a reader will be distracted by the readable content of a page when looking at its layout. The point of using Lorem Ipsum is that it has</p>
    <div class="btn" style="margin-top:49px">DONATE</div>
  </div>
</section>

<section class="video">
  <div class="abs rule" style="top:42px"></div>
  <h2 class="abs center sec-title" style="top:56px">OUR VIDEO</h2>
  <div class="abs rule" style="top:100px"></div>
  <div class="abs video-frame" role="img" aria-label="Video still: hand touching a holographic data dashboard">
    <div class="abs play"><svg width="24" height="24" viewBox="0 0 24 24"><path d="M6 3l15 9-15 9z" fill="#21c17a"/></svg></div>
  </div>
</section>

<section class="news">
  <div class="news-left abs">
    <div class="abs" style="left:296px;top:40px;width:104px;height:104px;border-radius:50%;background:#1a3450"></div>
    <svg class="abs" style="left:306px;top:66px" width="84" height="72" viewBox="0 0 84 72"><rect x="14" y="0" width="56" height="48" fill="#fff"/><path d="M22 12h40M22 20h40M22 28h26" stroke="#bbb" stroke-width="2"/><path d="M2 30l40 26 40-26v42H2z" fill="#cfd6df"/><path d="M2 72l40-26 40 26" fill="#e5e9ee"/></svg>
    <h3>Get notified about<br>new amazing products</h3>
    <div class="abs email"><svg width="14" height="11" viewBox="0 0 14 11"><rect width="14" height="11" fill="#fff"/><path d="M0 0l7 6 7-6" stroke="#0b1a30" fill="none"/></svg>Email</div>
    <div class="abs btn subscribe">Subscribe</div>
    <div class="abs consent"><span class="box"></span>By entering my email and subscribing I confirm and agree to the above.</div>
  </div>
  <div class="news-right abs">
    <hr style="top:101px">
    <h3>Never miss a drop</h3>
    <p class="tag">Subscribe for the latest news,<br>drops &amp; collectibles</p>
    <p class="fine">After reading the Privacy Notice, you may susbcribe for our \newsletter to get special offers and occasional surveys delivered to your inbox. Unsubscribe at any time by clicking on the link in the email.</p>
    <hr style="top:402px">
  </div>
</section>

<footer class="footer">
  <div class="abs brand" style="left:131px;top:46px;font-size:27px"><span class="brand-dot" style="width:44px;height:44px"></span>Giftwell Hub</div>
  <p class="abs about">There are many variations of passages of Lorem Ipsum available, but the majority have suffered alteration in some form, by injected humour, or randomised words which.</p>
  <div class="abs fcol" style="left:505px"><h5>MENU</h5>Home<br>About Us<br>Newsroom<br>Patemts<br>Clients<br>Faq<br>Contact</div>
  <div class="abs fcol" style="left:697px"><h5>ABOUT US</h5>Leadership<br>Careers<br>Partners<br>Blog<br>Nimbus Live<br>Testimonials<br>Resources</div>
  <div class="abs fcol" style="left:866px"><h5>FOLLOW US</h5>
    <div class="social"><span aria-label="Pixgram" style="background:#d9487a"></span><span aria-label="Friendnet"></span><span aria-label="Viewtube" style="background:#d93a3a"></span><span aria-label="Workrow" style="background:#3a7fc8"></span></div>
  </div>
  <div class="abs fline"></div>
  <p class="abs copy">Copyright © 2022 All Rights Reserved</p>
</footer>

</body>
</html>
```